Car rental website design for a UAE car rental company

This project is about creating a new website design for a car rental company located in Dubai (United Arab Emirates), I opened the same project a few months ago but I didn't receive a lot of appealing entries so I closed it but this time I am marking the project as guaranteed to avoid such situation again, if you have already provided a design before then please re-submit again on this project so that it is considered while reviewing all the designs

A few important things:

1- We need a simple non-complex design
2- The final deliverable would be 2 screens (PSD, JPEG ... etc), the first screen is for the home page and the second screen is for an internal page
3- The home page must have a section that end users can use to rent a car online directly from the home page instead of going into some inner pages
4- The current website is very old and not very appealing so avoid creating a similar design (www.crestvane-autos.example)
5- The name is Crestvane but the company rents normal cars (no Limousin cars will be rented) so avoid adding any fancy cars in the images/graphics used in the design, just normal end users cars
6- The expected pages would be: home, About us, Our team, Strategy, Contact us and links to social media pages
7- The attachments include the company's logo and some screens from other car rental companies that provide online rentals/payments

If you have any questions please feel free to ask and please note that we will need the designs urgently

Thanks

Target Market(s)

Dubai - United Arab Emirates

Industry/Entity Type

It Company

Number of Pages Required

2 page

Font styles to use
Sans Serif

Requirements
Must have
• Check the project details
Nice to have
Should not have

```html
<!DOCTYPE html>
<html lang="en">
<head>
<meta charset="utf-8">
<title>Crestvane Rent A Car</title>
<link href="https://fonts.googleapis.com/css2?family=Roboto+Slab:wght@300;400&family=Open+Sans:wght@400;600&display=swap" rel="stylesheet">
<style>
:root{
  --brand:#a8113f;
  --grey:#8a9690;
  --text:#333;
  --muted:#777;
  --light:#f3f3f3;
  --line:#cfcfcf;
}
*{box-sizing:border-box;margin:0;padding:0}
html,body{width:1121px;height:1200px;overflow:hidden;background:#fff}
body{position:relative;font-family:"Roboto Slab",serif;color:var(--text)}
a{color:inherit;text-decoration:none}

.site-header{position:absolute;left:0;top:0;width:1121px;height:97px;background:linear-gradient(#fff,#ededed);border-bottom:2px solid var(--line)}
.brand{position:absolute;left:75px;top:10px;display:flex;align-items:center;gap:10px}
.brand-mark{width:72px;height:80px;border:3px solid var(--brand);background:#fff}
.brand-name{font-size:36px;font-weight:400;color:var(--grey)}
.social{position:absolute;display:flex;gap:9px}
.social span{width:24px;height:24px;border-radius:50%;background:var(--grey);border:2px solid #fff;box-shadow:0 0 0 1px #bbb}
.header-social{left:563px;top:16px}
.call{position:absolute;left:788px;top:10px;display:flex;align-items:center;gap:8px;color:var(--brand);font-size:18px}
.main-nav{position:absolute;left:563px;top:66px;display:flex;gap:24px;font-size:16px;font-weight:300;color:var(--muted)}
.main-nav .active{color:var(--brand)}

.hero{position:absolute;left:0;top:97px;width:1121px;height:411px;border-bottom:3px solid var(--brand)}
.hero-photo{position:absolute;inset:0;background:radial-gradient(ellipse at 40% 55%,#c9ccd0 0%,#9ea3a8 45%,#6c7075 100%)}
.hero-title{position:absolute;left:85px;top:14px;width:320px;font-size:28px;line-height:35px;color:var(--brand);text-shadow:0 1px 3px rgba(255,255,255,.8)}
.booking{position:absolute;left:655px;top:2px;width:394px;height:406px;border:5px solid var(--brand);border-top:none;background:rgba(255,255,255,.78);font-size:13px}
.booking-tabs{display:flex;height:40px;background:var(--brand);color:#fff;font-size:14px}
.booking-tabs span{padding:12px 10px}
.booking-tabs .current{background:var(--grey);font-size:15px}
.step{position:absolute;left:6px;width:24px;height:24px;border:1px solid var(--brand);background:#fff;text-align:center;line-height:22px;font-size:14px}
.field-label{position:absolute;left:46px;font-size:13px}
.link{position:absolute;left:46px;color:var(--brand);text-decoration:underline;font-size:13px}
.input{position:absolute;height:25px;border:1px solid #999;background:rgba(255,255,255,.6);font-size:11px;padding:6px 7px}
.check{position:absolute;font-size:13px;display:flex;align-items:center;gap:5px}
.check i{width:9px;height:9px;border:1px solid #555;display:inline-block}
.help{display:inline-block;width:18px;height:18px;border-radius:50%;background:var(--grey);color:#fff;font-size:10px;text-align:center;line-height:18px;font-style:normal}
.quote-btn{position:absolute;right:9px;bottom:2px;width:128px;height:37px;background:var(--brand);color:#fff;font-size:15px;text-align:center;line-height:37px}

.features{position:absolute;left:0;top:511px;width:1121px;height:252px;background:var(--light);border-bottom:1px solid #ddd}
.feature{position:absolute;top:30px;width:250px;text-align:center}
.feature-icon{width:90px;height:90px;margin:0 auto;border-radius:50%;border:2px solid var(--grey);background:#fff;display:flex;align-items:center;justify-content:center}
.feature-icon.active{border-color:var(--brand)}
.feature h3{margin-top:22px;font-size:15px;font-weight:400;line-height:20px}
.feature p{margin-top:8px;font-family:"Open Sans",sans-serif;font-size:14px;line-height:19px;color:#555}

.content{position:absolute;left:78px;width:700px}
.content h2{font-size:18px;font-weight:300;color:var(--muted);padding-bottom:6px;border-bottom:1px dashed #aaa;width:436px}
.content h2 em{font-style:normal;color:var(--brand);font-weight:400}
.content p{font-size:13.5px;line-height:21px;margin-top:8px;font-weight:300;color:#222}
.read-more{display:block;margin-top:6px;font-size:14px}
.divider{position:absolute;left:78px;top:962px;width:700px;height:10px;background:radial-gradient(ellipse at 50% 0,rgba(0,0,0,.12),transparent 70%)}

.offer{position:absolute;left:834px;width:200px}
.offer-photo{height:110px;border-radius:40% 40% 10% 10%}
.offer-label{width:200px;height:38px;background:var(--grey);color:#fff;font-size:15px;text-align:center;line-height:38px;margin-top:-10px;position:relative}

.site-footer{position:absolute;left:0;top:1146px;width:1121px;height:54px;background:var(--brand);color:#fff}
.footer-nav{position:absolute;left:76px;top:19px;display:flex;gap:18px;font-size:14px;font-weight:300}
.footer-social{left:622px;top:15px}
.footer-social span{background:#d7d7d7}
.copyright{position:absolute;left:814px;top:19px;font-family:"Open Sans",sans-serif;font-size:13px}
</style>
</head>
<body>

<header class="site-header">
  <a class="brand" href="#"><span class="brand-mark"></span><span class="brand-name">Crestvane</span></a>
  <div class="social header-social"><span></span><span></span><span></span><span></span></div>
  <div class="call">
    <svg width="38" height="40" viewBox="0 0 38 40"><path d="M7 20a12 12 0 0 1 24 0" fill="none" stroke="#666" stroke-width="3"/><rect x="3" y="18" width="8" height="13" rx="3" fill="#a8113f"/><rect x="27" y="18" width="8" height="13" rx="3" fill="#a8113f"/><path d="M31 31q0 6-10 6" fill="none" stroke="#666" stroke-width="2"/></svg>
    Call us at +971 4 000 1234
  </div>
  <nav class="main-nav"><a class="active" href="#">HOME</a><a href="#">ABOUT US</a><a href="#">OUR TEAM</a><a href="#">STRATEGY</a><a href="#">CONTACT US</a></nav>
</header>

<section class="hero">
  <div class="hero-photo" role="img" aria-label="Silver coupe parked in a grey studio"></div>
  <h1 class="hero-title">Experience An Extra Mile of comfort, pleasure and leisure From the best</h1>
  <form class="booking">
    <div class="booking-tabs"><span class="current">Book A Car</span><span>View / Modify / Cancel A Reservation</span></div>
    <span class="step" style="top:55px">1</span>
    <span class="field-label" style="top:56px">Pick-up Location &nbsp;(City, State or Airport Code</span>
    <span class="link" style="top:77px">Previous Searches</span>
    <div class="input" style="left:46px;top:100px;width:325px">Dubai Airport - Terminal 3</div>
    <span class="link" style="top:133px">Help me find a rental location</span>
    <span class="check" style="left:46px;top:157px"><i></i>Return car to a different Crestvane Location <span class="help">?</span></span>
    <span class="step" style="top:192px">2</span>
    <span class="field-label" style="top:192px">Pick-up Date &amp; Time</span>
    <div class="input" style="left:46px;top:215px;width:160px">26/03/2015</div>
    <div class="input" style="left:211px;top:215px;width:160px">16:00</div>
    <span class="field-label" style="top:252px">Return Date &amp; Time</span>
    <div class="input" style="left:46px;top:275px;width:160px">26/03/2015</div>
    <div class="input" style="left:211px;top:275px;width:160px">16:00</div>
    <span class="field-label" style="top:313px">Hire Car Type</span>
    <div class="input" style="left:46px;top:336px;width:160px;font-size:12px">Automatic</div>
    <span class="check" style="left:214px;top:336px"><i></i>Apply a discount Code <span class="help">?</span></span>
    <span class="quote-btn">Get A Quote</span>
  </form>
</section>

<section class="features">
  <div class="feature" style="left:63px">
    <div class="feature-icon active"><svg width="60" height="44" viewBox="0 0 60 44"><path d="M4 22l5-10h20l5 10v10H4z" fill="#a8113f"/><circle cx="11" cy="32" r="4" fill="#fff"/><circle cx="27" cy="32" r="4" fill="#fff"/><path d="M24 30l5-10h20l5 10v10H24z" fill="#a8113f" stroke="#fff" stroke-width="2"/><circle cx="31" cy="40" r="3.5" fill="#fff"/><circle cx="47" cy="40" r="3.5" fill="#fff"/></svg></div>
    <h3>Wide Range Of Vehicles For City Driving or SUV’s For Trips</h3>
    <p>Lorem ipsum dolor sit aonsectetuer adipiscing elied diam nonummy</p>
  </div>
  <div class="feature" style="left:326px">
    <div class="feature-icon"><svg width="44" height="44" viewBox="0 0 44 44"><path d="M20 6h14v14L18 36 6 24z" fill="#8a9690"/><circle cx="28" cy="12" r="2.5" fill="#fff"/><text x="15" y="27" font-size="9" fill="#fff" font-family="sans-serif">%</text></svg></div>
    <h3>Special 10% Discount For New Customers On The First Rent</h3>
    <p>Lorem ipsum dolor sit aonsectetuer adipiscing elied diam nonummy</p>
  </div>
  <div class="feature" style="left:576px">
    <div class="feature-icon"><svg width="44" height="50" viewBox="0 0 44 50"><circle cx="13" cy="9" r="6" fill="#8a9690"/><rect x="17" y="7" width="18" height="4" fill="#8a9690"/><path d="M6 34l5-10h22l5 10v10H6z" fill="#8a9690"/><circle cx="13" cy="44" r="3.5" fill="#fff"/><circle cx="31" cy="44" r="3.5" fill="#fff"/></svg></div>
    <h3>Long Term Car<br>Rentals</h3>
    <p>Lorem ipsum dolor sit aonsectetuer adipiscing elied diam nonummy</p>
  </div>
  <div class="feature" style="left:826px">
    <div class="feature-icon"><svg width="44" height="44" viewBox="0 0 44 44"><path d="M16 10L6 18l10 8" fill="none" stroke="#8a9690" stroke-width="5" stroke-linejoin="round"/><path d="M8 18h16a10 10 0 0 1 0 20h-2" fill="none" stroke="#8a9690" stroke-width="5"/></svg></div>
    <h3>Buyback Option After<br>Lease Term</h3>
    <p>Lorem ipsum dolor sit aonsectetuer adipiscing elied diam nonummy</p>
  </div>
</section>

<article class="content" style="top:792px">
  <h2>Welcome to Crestvane <em>Rent A Car</em></h2>
  <p>As Dubai is expected to welcome millions of tourists and visitors, car rental industry is believed to escalate more rapidly in the region. Over the past five years, demands for car rentals in Dubai has been augmenting at a healthy pace and is currently registering a growth rate of 20 to 25 percent per year. The swift economic growth and the number. Crestvane was established to bring comfort and pleasure to all its clients. ...</p>
  <a class="read-more" href="#">Read More</a>
</article>
<div class="divider"></div>
<article class="content" style="top:1000px">
  <h2>Our <em>Mission</em></h2>
  <p>To be one of the leading auto leasing company in the fast growing economy and tourism industry of the emirate of Dubai &amp; play alongside with the major car rental companies in the globe.</p>
  <p style="margin-top:2px">Crestvane vows to deliver comfort, luxury &amp; satisfaction to all our clients by providing them professional, hassle-free and first class service.</p>
</article>

<aside class="offer" style="top:790px">
  <div class="offer-photo" role="img" aria-label="Silver sedan" style="background:linear-gradient(#eceeef,#a9adb1)"></div>
  <div class="offer-label">From Only AED 1100 p/m</div>
</aside>
<aside class="offer" style="top:990px">
  <div class="offer-photo" role="img" aria-label="Red sedan" style="background:linear-gradient(#f08a8a,#c21a1a)"></div>
  <div class="offer-label">From Only AED 1100 p/m</div>
</aside>

<footer class="site-footer">
  <nav class="footer-nav"><a href="#">HOME</a><a href="#">ABOUT US</a><a href="#">OUR TEAM</a><a href="#">STRATEGY</a><a href="#">CONTACT US</a></nav>
  <div class="social footer-social"><span></span><span></span><span></span><span></span></div>
  <p class="copyright">© 2015 Crestvane. All Rights Reserved</p>
</footer>

</body>
</html>
```